Birchline Septic Solutions

Would like to see some single sided ones but would also like to see some double sided with one sided only being the logo. Owners name is Colin Vandro. Phone number is 555-214-0387
Services are pumping, inspections, installs, and repairs

Contact Information for Business Card

555-241-0387 Colin Vandro Maple Hollow, OH

```html
<!DOCTYPE html>
<html lang="en">
<head>
<meta charset="utf-8">
<title>Birchline Septic Solutions – Business Cards</title>
<link href="https://fonts.googleapis.com/css2?family=Montserrat:wght@500;600;800&display=swap" rel="stylesheet">
<style>
  :root {
    --backdrop: #b7b7b7;
    --ink: #000000;
    --paper: #ffffff;
    --teal: #2bbfb6;
    --rule: #8c8c8c;
  }
  * { margin: 0; padding: 0; box-sizing: border-box; }
  html, body {
    width: 1200px; height: 1200px; overflow: hidden;
    background: var(--backdrop);
    font-family: "Montserrat", sans-serif;
  }
  .stage { position: relative; width: 1200px; height: 1200px; }
  .card {
    position: absolute; top: 303px;
    width: 366px; height: 594px;
    background: var(--paper); overflow: hidden;
  }
  .card--back { left: 200px; }
  .card--front { left: 599px; }

  /* Back: services */
  .back__dark {
    position: absolute; left: 0; top: 0; width: 100%; height: 438px;
    background: var(--ink);
  }
  .services {
    position: absolute; top: 134px; width: 100%;
    list-style: none; text-align: center;
    color: var(--paper); font-weight: 600; font-size: 30px;
    line-height: 42px; letter-spacing: 0.5px;
  }

  /* Business name, set as plain text */
  .brand {
    position: absolute; left: 0; width: 100%;
    text-align: center; color: var(--ink); font-weight: 800;
  }
  .brand__word, .brand__sub { display: block; }
  .brand--back { top: 449px; }
  .brand--back .brand__word { font-size: 48px; line-height: 56px; letter-spacing: 1px; }
  .brand--back .brand__sub { margin-top: 8px; font-size: 20px; line-height: 26px; letter-spacing: 4px; }
  .brand--front { top: 164px; }
  .brand--front .brand__word { font-size: 40px; line-height: 48px; letter-spacing: 1px; }
  .brand--front .brand__sub { margin-top: 8px; font-size: 18px; line-height: 24px; letter-spacing: 4px; }

  /* Front: contact */
  .holder {
    position: absolute; top: 322px; width: 100%;
    text-align: center; font-weight: 800; font-size: 24px; color: var(--ink);
  }
  .contact { position: absolute; left: 0; width: 100%; text-align: center; }
  .contact--phone { top: 374px; }
  .contact--place { top: 449px; }
  .contact__divider { display: block; margin: 0 auto; }
  .contact__text {
    margin-top: 6px; font-weight: 500; font-size: 19px; color: var(--ink); letter-spacing: 0.5px;
  }
</style>
</head>
<body>
<main class="stage">
  <section class="card card--back">
    <div class="back__dark"></div>
    <ul class="services">
      <li>PUMPING</li>
      <li>INSPECTIONS</li>
      <li>INSTALLS</li>
      <li>REPAIRS</li>
    </ul>
    <p class="brand brand--back">
      <span class="brand__word">BIRCHLINE</span>
      <span class="brand__sub">SEPTIC SOLUTIONS</span>
    </p>
  </section>

  <section class="card card--front">
    <p class="brand brand--front">
      <span class="brand__word">BIRCHLINE</span>
      <span class="brand__sub">SEPTIC SOLUTIONS</span>
    </p>

    <h1 class="holder">COLIN VANDRO</h1>

    <div class="contact contact--phone">
      <svg class="contact__divider" width="220" height="40" viewBox="0 0 220 40" aria-hidden="true">
        <line x1="2" y1="20" x2="78" y2="20" stroke="var(--rule)" stroke-width="1.5"/>
        <line x1="142" y1="20" x2="218" y2="20" stroke="var(--rule)" stroke-width="1.5"/>
        <circle cx="110" cy="20" r="18" fill="none" stroke="var(--teal)" stroke-width="1.8"/>
        <path d="M103 13c1-1 2-1 3 0l2 3c.5 1 .3 1.6-.5 2.2l-1 .8c1 2 2.5 3.5 4.5 4.5l.8-1c.6-.8 1.3-1 2.2-.5l3 2c1 .7 1 1.8 0 2.8l-1.2 1.2c-1.5 1.5-4 1-7-1.2s-5.5-5-7-7.8-1.7-5-.2-6.5z" fill="var(--teal)"/>
      </svg>
      <p class="contact__text">555-214-0387</p>
    </div>

    <div class="contact contact--place">
      <svg class="contact__divider" width="220" height="40" viewBox="0 0 220 40" aria-hidden="true">
        <line x1="2" y1="20" x2="78" y2="20" stroke="var(--rule)" stroke-width="1.5"/>
        <line x1="142" y1="20" x2="218" y2="20" stroke="var(--rule)" stroke-width="1.5"/>
        <circle cx="110" cy="20" r="18" fill="none" stroke="var(--teal)" stroke-width="1.8"/>
        <path d="M110 29c-4-5-6-8-6-11a6 6 0 0 1 12 0c0 3-2 6-6 11z" fill="var(--teal)"/>
        <circle cx="110" cy="18" r="2" fill="var(--paper)"/>
      </svg>
      <p class="contact__text">Maple Hollow, OH</p>
    </div>
  </section>
</main>
</body>
</html>
```